Business Card Design

I already have a company logo for my company. I have a logo for the manufacturer we represent. I want a professional business card design.

```html
<!DOCTYPE html>
<html lang="en">
<head>
<meta charset="utf-8">
<title>Harbor Signal LLC – Business Card</title>
<link rel="stylesheet" href="https://fonts.googleapis.com/css2?family=Open+Sans:wght@400;700&display=swap">
<style>
  :root {
    --bg: #3a3a3a;
    --card: #161616;
    --red: #e31e26;
    --gold: #e0a526;
    --white: #f2f2f2;
    --muted: #dcdcdc;
  }
  * { margin: 0; padding: 0; box-sizing: border-box; }
  html, body {
    width: 1200px; height: 780px; overflow: hidden;
    background: var(--bg);
    font-family: "Open Sans", Arial, sans-serif;
  }
  .stage {
    position: relative; width: 1200px; height: 780px;
    display: flex; align-items: center; justify-content: center; gap: 40px;
  }
  .card {
    position: relative; width: 520px; height: 300px;
    background: var(--card); border-radius: 22px; overflow: hidden;
    box-shadow: 0 14px 30px rgba(0,0,0,.45);
  }
  /* brand lockup */
  .brand {
    display: flex; align-items: center; gap: 10px;
    color: var(--white); font-weight: 700; letter-spacing: 1px;
    text-transform: uppercase; line-height: 1;
  }
  .brand-mark { width: 16px; height: 16px; background: var(--red); flex: none; }
  .brand-name span { display: block; }
  /* front */
  .front .brand {
    position: absolute; left: 34px; top: 100px; width: 220px;
    font-size: 22px; line-height: 1.15;
  }
  .front .divider {
    position: absolute; left: 276px; top: 44px; width: 1px; height: 180px;
    background: var(--red);
  }
  .contact { position: absolute; left: 296px; top: 48px; color: var(--muted); font-size: 14px; }
  .contact .name { color: var(--red); font-weight: 700; font-size: 21px; text-transform: uppercase; letter-spacing: .5px; line-height: 1.1; }
  .contact .role { color: var(--white); font-size: 14px; margin-bottom: 10px; }
  .contact ul { list-style: none; }
  .contact li { display: flex; align-items: center; gap: 7px; line-height: 1.55; }
  .contact li svg { width: 12px; height: 12px; fill: var(--red); flex: none; }
  .contact .address { margin-top: 6px; line-height: 1.45; }
  .edge-stripes { position: absolute; left: 0; bottom: 0; width: 100%; height: 30px; }
  /* back */
  .back { display: flex; align-items: center; justify-content: center; }
  .back .brand { font-size: 30px; gap: 14px; }
  .back .brand-mark { width: 22px; height: 22px; }
  .back .brand-name span { display: inline; }
</style>
</head>
<body>
<main class="stage">
  <section class="card front" aria-label="Business card front">
    <div class="brand"><span class="brand-mark"></span><span class="brand-name"><span>Harbor Signal</span><span>LLC</span></span></div>
    <div class="divider"></div>
    <div class="contact">
      <p class="name">Daniel Reyes</p>
      <p class="role">Managing Director</p>
      <ul>
        <li><svg viewBox="0 0 24 24"><path d="M6.6 10.8a15.1 15.1 0 0 0 6.6 6.6l2.2-2.2c.3-.3.7-.4 1-.2 1.1.4 2.3.6 3.6.6.6 0 1 .4 1 1V20c0 .6-.4 1-1 1C10.6 21 3 13.4 3 4c0-.6.4-1 1-1h3.5c.6 0 1 .4 1 1 0 1.3.2 2.5.6 3.6.1.3 0 .7-.2 1z"/></svg>555 014 2290</li>
        <li><svg viewBox="0 0 24 24"><path d="M2 5h20v14H2zm2 2v.5l8 5 8-5V7l-8 5z"/></svg>hello@harborsignal.com</li>
        <li><svg viewBox="0 0 24 24"><circle cx="12" cy="12" r="10"/></svg>www.harborsignal.com</li>
      </ul>
      <p class="address">Your address, City<br>State, Zip 1234</p>
    </div>
    <svg class="edge-stripes" viewBox="0 0 520 30" preserveAspectRatio="none" aria-hidden="true">
      <rect x="0" y="12" width="232" height="5" fill="var(--gold)"/>
      <rect x="0" y="19" width="232" height="11" fill="var(--white)"/>
      <polygon points="230,8 520,8 520,30 222,30" fill="var(--red)"/>
    </svg>
  </section>

  <section class="card back" aria-label="Business card back">
    <div class="brand"><span class="brand-mark"></span><span class="brand-name"><span>Harbor Signal</span> <span>LLC</span></span></div>
  </section>
</main>
</body>
</html>
```